RPM/CCM Marketing Book

We need a new logo designed for the company,
Quillmark Assaying, some logo ideas are attached.

We would like this book revamped with a new design as well as included updates made in line with the design and text. Please let me know of any clarifications or follow-up questions that possible can come up. The old booklet is attached as well which is to be used for the new design.

```html
<!DOCTYPE html>
<html lang="en">
<head>
<meta charset="utf-8">
<title>RPM / CCM Marketing Book 2023</title>
<link href="https://fonts.googleapis.com/css2?family=Roboto+Condensed:wght@400;700&family=Arimo:wght@400;700&display=swap" rel="stylesheet">
<style>
:root{
  --stage:#333333;
  --blue:#1fa9e1;
  --blue-soft:#9dd3f0;
  --gray:#898a8e;
  --gray-dark:#6f7074;
  --white:#ffffff;
  --ink:#3c3c3c;
  --ink-soft:#5a5a5a;
  --head:"Roboto Condensed",Arial,sans-serif;
  --body:"Arimo",Arial,sans-serif;
}
*{box-sizing:border-box;margin:0;padding:0}
html,body{width:1200px;height:2832px;overflow:hidden;background:var(--stage)}
body{position:relative;font-family:var(--body);color:var(--ink)}
.page{position:absolute;overflow:hidden;background:var(--white)}
.abs{position:absolute}
.photo{position:absolute}
.brand{position:absolute;font-family:var(--body);font-weight:700;color:var(--blue);font-size:9px;letter-spacing:.2px;display:flex;align-items:center;gap:4px}
.brand .dot{width:8px;height:8px;border-radius:50%;background:var(--blue)}
.url{position:absolute;font-size:7.5px;color:var(--ink-soft)}
.spine{position:absolute;writing-mode:vertical-rl;transform:rotate(180deg);font-size:5px;letter-spacing:1.5px;color:var(--white);font-weight:700}
.tab{position:absolute;background:var(--blue)}

/* cover */
.cover{left:604px;top:102px;width:486px;height:630px}
.cover .codes{left:0;width:100%;top:515px;text-align:center;color:var(--white);font-family:var(--body);font-weight:700;font-size:18px;letter-spacing:.3px}
.cover .codes i{color:var(--gray);font-style:normal;font-size:12px;margin:0 4px}
.cover .year{left:0;width:100%;top:547px;text-align:center;color:var(--white);font-size:20px}
.cover .site{left:0;width:100%;top:585px;text-align:center;color:var(--ink-soft);font-weight:700;font-size:14px}

/* contents */
.contents{left:119px;top:763px;width:971px;height:628px;background:var(--gray)}
.contents h1{position:absolute;right:308px;top:102px;text-align:right;font-family:var(--body);color:var(--white);font-size:22px;line-height:27px;font-weight:400}
.toc{position:absolute;left:689px;top:102px;width:242px;list-style:none}
.toc li{display:flex;justify-content:space-between;align-items:flex-end;font-size:7.2px;color:var(--white);line-height:9px;margin-bottom:6.2px}
.toc li.main{color:var(--blue);font-weight:700;font-size:8.8px;margin-top:8px}
.toc li.main:first-child{margin-top:0}
.toc li.sub{padding-left:17px}
.toc li span:last-child{color:var(--blue);min-width:12px;text-align:right}

/* outsourcing spread */
.spread{left:123px;top:1423px;width:967px;height:626px}
.spread .leftpanel{left:0;top:0;width:456px;height:462px;background:var(--gray)}
.company{left:42px;top:112px;color:var(--white);font-size:9px;font-weight:700;display:flex;align-items:center;gap:4px}
.company .sq{width:8px;height:8px;background:var(--blue)}
.spread h2{position:absolute;left:44px;top:146px;font-family:var(--head);font-weight:700;font-size:34px;color:var(--white);line-height:1}
.spread h2 em{font-style:normal;color:var(--blue)}
.spread .sub{left:44px;top:196px;font-family:var(--head);font-weight:700;font-size:15px;color:var(--white);line-height:19px}
.compare{position:absolute;left:44px;top:242px;width:411px;border-collapse:collapse;font-size:7px;line-height:8.4px;color:var(--ink)}
.compare th{background:var(--blue);color:var(--white);text-align:left;font-weight:400;font-size:10px;padding:3px 6px;border:1px solid var(--white)}
.compare td{background:#e4e4e4;padding:2px 6px;border:1px solid var(--gray-dark);vertical-align:top;width:50%}
.compare td.calls{background:var(--blue-soft);height:85px}
.compare td.calls b{font-weight:700;display:block;margin-bottom:9px}
.benefits-title{left:44px;top:474px;font-family:var(--head);font-weight:700;font-size:15px;color:var(--ink)}
.benefits-title em{font-style:normal;color:var(--blue)}
.benefits{position:absolute;left:59px;top:502px;font-size:9px;line-height:11.2px;color:var(--ink-soft)}
.side-strip{left:16px;top:462px;width:10px;height:164px}
.start-title{left:552px;top:70px;font-family:var(--head);font-weight:700;font-size:35px;color:var(--blue)}
.steps{position:absolute;font-size:7.4px;line-height:8.8px;color:var(--ink-soft);list-style:none}
.steps li{display:flex;gap:6px;margin-bottom:9px}
.steps li b{font-weight:400;min-width:10px}
.note{left:483px;top:481px;width:457px;height:145px;background:var(--blue);color:var(--white);font-size:5.2px;line-height:6.4px;padding:13px 0 0 30px;display:flex;gap:14px}
.note div{width:190px}
.note p{margin-bottom:6px}
.note-strip{left:940px;top:481px;width:27px;height:145px;background:var(--gray)}

/* chronic care page */
.ccm{left:123px;top:2080px;width:488px;height:626px;background:var(--gray)}
.ccm h2{position:absolute;left:89px;top:70px;font-family:var(--head);font-weight:700;font-size:33px;color:var(--blue)}
.ccm h3{position:absolute;font-family:var(--head);font-weight:700;color:var(--white);font-size:14.5px;text-align:center;width:250px;left:218px}
.ccm .para{position:absolute;left:218px;width:250px;font-size:7.6px;line-height:9.3px;color:var(--white);text-align:center}
.ccm .para p{margin-bottom:9px}
.perk{position:absolute;left:250px;width:220px;display:flex;gap:10px;color:var(--white);font-size:7.2px;line-height:8.8px}
.perk .ico{width:22px;height:22px;flex:none}
.perk b{display:block}
</style>
</head>
<body>

<!-- Cover -->
<section class="page cover">
  <svg class="photo" width="486" height="630" viewBox="0 0 486 630">
    <defs>
      <linearGradient id="coverPhoto" x1="0" y1="0" x2="1" y2="1">
        <stop offset="0" stop-color="#c9d2d8"/>
        <stop offset="0.5" stop-color="#9aa7b3"/>
        <stop offset="1" stop-color="#4d6f93"/>
      </linearGradient>
    </defs>
    <rect width="486" height="480" fill="url(#coverPhoto)" role="img" aria-label="Photo: physician with laptop consulting a patient in a clinic"/>
    <path d="M0 460 C90 410 200 420 290 440 C370 455 430 430 486 410 L486 580 L0 580 Z" fill="var(--gray)"/>
    <path d="M0 465 C100 430 220 470 300 470 C380 470 440 450 486 440 L486 580 L0 580 Z" fill="var(--blue)"/>
    <rect y="580" width="486" height="50" fill="#fff"/>
  </svg>
  <div class="brand" style="left:70px;top:342px;color:var(--blue);background:#fff;padding:4px 8px"><span class="dot"></span>QUILLMARK ASSAYING</div>
  <div class="abs codes">RPM<i>•</i>CCM<i>•</i>RTM<i>•</i>CPM<i>•</i>BHI<i>•</i>TCM<i>•</i>PCM</div>
  <div class="abs year">2023</div>
  <div class="abs site">www.ridgewaycare.example</div>
</section>

<!-- Table of contents -->
<section class="page contents">
  <svg class="photo" width="971" height="628" viewBox="0 0 971 628">
    <defs>
      <linearGradient id="tocPhoto" x1="0" y1="0" x2="1" y2="0">
        <stop offset="0" stop-color="#e8ebee"/>
        <stop offset="0.6" stop-color="#7ba3c4"/>
        <stop offset="1" stop-color="#cfd6dc"/>
      </linearGradient>
    </defs>
    <polygon points="0,0 447,0 490,628 0,628" fill="url(#tocPhoto)" role="img" aria-label="Photo: smiling nurse in blue scrubs with stethoscope, colleague behind"/>
  </svg>
  <div class="url" style="left:736px;top:45px;color:#fff">www.ridgewaycare.example</div>
  <div class="brand" style="left:840px;top:43px"><span class="dot"></span>QUILLMARK ASSAYING</div>
  <h1>TABLE OF<br>CONTENTS</h1>
  <ul class="toc">
    <li class="main"><span>1.&nbsp;&nbsp; The case for doing monitoring in-house.</span><span>1</span></li>
    <li class="main"><span>2.&nbsp;&nbsp; How to Get Started</span><span>2</span></li>
    <li class="main"><span>3.&nbsp;&nbsp; Chronic Care Management (CCM)</span><span>3</span></li>
    <li class="sub"><span>a.&nbsp; Who can perform CCM</span><span>4</span></li>
    <li class="sub"><span>b.&nbsp; CCM Results</span><span>4</span></li>
    <li class="sub"><span>c.&nbsp; Who is Eligible for CCM</span><span>5</span></li>
    <li class="sub"><span>d.&nbsp; CCM Care Plan</span><span>6</span></li>
    <li class="sub"><span>e.&nbsp; Classic vs Complex CCM</span><span>8</span></li>
    <li class="sub"><span>f.&nbsp; CCM CPT Codes</span><span>8</span></li>
    <li class="sub"><span>g.&nbsp; CCM Patient Scenarios</span><span>9</span></li>
    <li class="main"><span>4.&nbsp;&nbsp; Remote Patient Monitoring (RPM)</span><span>12</span></li>
    <li class="sub"><span>a.&nbsp; Featured Equipment</span><span>12</span></li>
    <li class="sub"><span>b.&nbsp; Benefits of RPM</span><span>15</span></li>
    <li class="sub"><span>c.&nbsp; RPM Requirements</span><span>16</span></li>
    <li class="sub"><span>d.&nbsp; RPM Benefits for Patients<br>&nbsp;&nbsp;&nbsp;&nbsp;with Chronic Conditions</span><span>18</span></li>
    <li class="sub"><span>e.&nbsp; RPM Benefits for Patients<br>&nbsp;&nbsp;&nbsp;&nbsp;with Diabetes</span><span>19</span></li>
    <li class="sub"><span>f.&nbsp; RPM Use for Chronic Conditions</span><span>20</span></li>
    <li class="sub"><span>g.&nbsp; Advantages of Incorporating Telehealth<br>&nbsp;&nbsp;&nbsp;&nbsp;&amp; RPM into Diabetes Care Management</span><span>21</span></li>
    <li class="sub"><span>h.&nbsp; Why Remote Monitoring is Essential to<br>&nbsp;&nbsp;&nbsp;&nbsp;Manage High Blood Pressure</span><span>24</span></li>
    <li class="sub"><span>i.&nbsp; RPM Key Features of the Program</span><span>27</span></li>
    <li class="sub"><span>j.&nbsp; RPM CPT Codes</span><span>29</span></li>
    <li class="main"><span>5.&nbsp;&nbsp; Potential Revenue</span><span>30</span></li>
    <li class="sub"><span>a.&nbsp; RPM Revenue</span><span>30</span></li>
    <li class="sub"><span>b.&nbsp; CCM Revenue</span><span>32</span></li>
  </ul>
  <div class="spine" style="left:946px;top:430px">RPM / CCM • 2023</div>
  <div class="tab" style="left:946px;top:590px;width:10px;height:38px"></div>
</section>

<!-- Outsourcing / Getting started spread -->
<section class="page spread">
  <div class="abs leftpanel"></div>
  <div class="abs company"><span class="sq"></span>RIDGEWAY CARE, LLC</div>
  <h2>The Case for <em>Outsourcing</em></h2>
  <div class="abs sub">Remote Patient Monitoring/Chronic Care Management<br>to a trusted 3rd party Ridgeway Care LLC</div>
  <table class="compare">
    <tr><th>CCM</th><th>RPM</th></tr>
    <tr><td>24/7 Access call center<br>Ridgeway Care acts as an extension of your care coordination team so that your patients with chronic conditions have access to a clinician, 24/7.</td>
        <td>Monitoring program collects wide range of health data from the point of care, vital signs, weight, blood pressure, blood sugar, blood oxygen, heart rate, and electrocardiograms.</td></tr>
    <tr><td>Certified Medical Staff</td><td>Certified Medical Staff</td></tr>
    <tr><td>Ridgeway Care will develop a comprehensive care plan per Medicare regulations for CCM.</td><td>Equipment works on Cellular network no need for patient to have internet service.</td></tr>
    <tr><td>Facilitating communication between all of health-care providers and patients.</td><td>Installation and Ordering of RPM Equipment and Setting up the equipment in patients home.</td></tr>
    <tr><td class="calls" colspan="2"><b>MONTHLY CALLS INCLUDE:</b>1. Review of medications<br>2. Discussion of test results<br>3. Exercise and therapy options<br>4. Scheduling regular or unanticipated office visits with the primary provider<br>5. Referrals to specialists, as needed<br>6. Provide Education on the patients Chronic Conditions</td></tr>
  </table>
  <div class="abs benefits-title"><em>MEDICAL</em> Offices Benefits:</div>
  <ul class="benefits">
    <li>Keep your workflow No Staff, No Space or Scheduling from your staff needed</li>
    <li>Reduce scheduling burden from front office</li>
    <li>Immediate Revenue</li>
    <li>New Income Stream</li>
    <li>Improve your MIPS Score</li>
    <li>Able to provide Telemedicine Visits on patients who are participating in Ridgeway Care<br>RPM/CCM program</li>
    <li>Increase Patient Satisfaction</li>
  </ul>
  <div class="spine" style="left:16px;top:505px;color:var(--ink-soft)">RPM / CCM • 2023</div>
  <div class="tab" style="left:16px;top:584px;width:10px;height:42px"></div>

  <div class="url" style="left:735px;top:45px">www.ridgewaycare.example</div>
  <div class="brand" style="left:838px;top:42px"><span class="dot"></span>QUILLMARK ASSAYING</div>
  <div class="abs start-title">How to Get Started:</div>
  <ol class="steps" style="left:553px;top:124px;width:205px">
    <li><b>1.</b><span>Practice discusses with patient if Patient is interested in RPM and/or CCM program.</span></li>
    <li><b>2.</b><span>Practice by fax or online intake submits an initial order for RPM and/or CCM with the patient H&amp;P.</span></li>
    <li><b>3.</b><span>We will contact each patient on your behalf and explain the CCM and RPM program.</span></li>
    <li><b>4.</b><span>The patient must opt into CCM and RPM program by signing a consent.</span></li>
  </ol>
  <ol class="steps" style="left:768px;top:124px;width:172px">
    <li><b>5.</b><span>The patient can also opt out of the program at any time, at the end of the calendar month.</span></li>
    <li><b>6.</b><span>We will go to patients' home explain and educate on the program and obtain the signature on the consent forms.</span></li>
    <li><b>7.</b><span>We will order and install all the equipment in the patient's home.</span></li>
    <li><b>8.</b><span>RPM/CCM services are done under Prescribing Physician General Supervision*see bellow CMS definitions</span></li>
    <li><b>9.</b><span>Only the prescribing physician can bill for the RPM/CCM Service.</span></li>
    <li><b>10.</b><span>Ridgeway Care can bill for CCM/RPM directly on physician behalf.</span></li>
    <li><b>11.</b><span>The required time for RPM/CCM will be documented in the EHR system of Ridgeway Care.</span></li>
    <li><b>12.</b><span>The EHR System is cloud based and the Physician shall have complete access to his patient charts.</span></li>
    <li><b>13.</b><span>At Physician discretion Ridgeway Care can upload and document the patient encounters in the Physician current EHR system. We can also provide electronic documentation to the Physician staff, for Physician staff to update the patient chart in Physician EHR.</span></li>
  </ol>
  <svg class="photo" style="left:454px;top:242px" width="308" height="220" viewBox="0 0 308 220">
    <defs>
      <linearGradient id="officePhoto" x1="0" y1="0" x2="1" y2="1">
        <stop offset="0" stop-color="#8a7565"/>
        <stop offset="0.55" stop-color="#c9c4bf"/>
        <stop offset="1" stop-color="#e9ecee"/>
      </linearGradient>
    </defs>
    <rect width="308" height="220" fill="url(#officePhoto)" role="img" aria-label="Photo: doctor shaking hands with a couple at an office desk"/>
  </svg>
  <div class="abs note">
    <div>
      <p>* CCM and RPM qualify as designated care management services under 42 CFR 410.26(b)(5). Meaning these services can be furnished under the general supervision (as opposed to direct supervision) of a physician or practitioner.</p>
      <p>Billing practitioner may arrange to have clinical staff external to the practice (e.g., a case management company) provide care management services for his or her patients, but only if all requirements for "incident to" billing are satisfied, including general supervision.</p>
    </div>
    <div>
      <p>Clinical Staff: a person who works under the supervision of a physician or other qualified healthcare professional and who is allowed by law, regulation, and facility policy to perform or assist in the performance of a specified professional service, but who does not individually report that professional service.</p>
      <p>Incident to Billing: physician or other practitioner billing for the service must be the same individual who provides general supervision of the clinical staff.</p>
      <p>General Supervision: general supervision (i.e., physician or other practitioner available by telephone to provide</p>
    </div>
  </div>
  <div class="abs note-strip"></div>
  <div class="spine" style="left:945px;top:505px">RPM / CCM • 2023</div>
</section>

<!-- Chronic Care Management -->
<section class="page ccm">
  <svg class="photo" width="230" height="626" viewBox="0 0 230 626">
    <defs>
      <linearGradient id="coatPhoto" x1="0" y1="0" x2="1" y2="0">
        <stop offset="0" stop-color="#f1f1f1"/>
        <stop offset="0.7" stop-color="#dcdcdc"/>
        <stop offset="1" stop-color="#898a8e"/>
      </linearGradient>
    </defs>
    <rect width="230" height="626" fill="url(#coatPhoto)" role="img" aria-label="Photo: doctor in white coat holding a stethoscope"/>
  </svg>
  <div class="spine" style="left:16px;top:500px;color:var(--ink-soft)">RPM / CCM • 2023</div>
  <div class="tab" style="left:16px;top:590px;width:10px;height:36px"></div>
  <h2>Chronic Care Management</h2>
  <h3 style="top:130px">Overview</h3>
  <h3 style="top:161px">What is Chronic Care Management?</h3>
  <div class="para" style="top:186px">
    <p>Chronic Care Management (CCM) offers personal support to patients with complex needs. This added level of care and service leads patients to a healthier lifestyle by proactively managing their care and providing a trusted clinical resource they can reach around-the-clock.</p>
    <p>CCM is designed for patients with two or more chronic conditions that are anticipated to last at least 12 months or until the patient's death.</p>
    <p>Patients enrolled in CCM services benefit from an entire care team focused on their needs, increased communication with their provider and improved care coordination.</p>
  </div>
  <h3 style="top:331px">CCM Benefits</h3>
  <div class="para" style="top:354px">
    <p>Two thirds of patients on Medicare have two or more chronic conditions, which means many patients can benefit from CCM services. CCM can help your clinic deliver coordinated care to patients that need additional time and resources between appointments. Benefits to your clinic include:</p>
  </div>
  <div class="perk" style="top:424px">
    <svg class="ico" viewBox="0 0 22 22"><rect x="2" y="5" width="18" height="14" rx="2" fill="#fff"/><rect x="8" y="2" width="6" height="4" fill="none" stroke="#fff" stroke-width="1.5"/><path d="M11 8v8M7 12h8" stroke="var(--blue)" stroke-width="2.5"/></svg>
    <div><b>Better Patient Outcomes</b>Patients gain a supportive healthcare team dedicated to creating a comprehensive care plan.</div>
  </div>
  <div class="perk" style="top:472px">
    <svg class="ico" viewBox="0 0 22 22"><path d="M11 18 C4 13 3 9 5 6 C7 4 10 5 11 7 C12 5 15 4 17 6 C19 9 18 13 11 18Z" fill="var(--blue)"/><path d="M2 12 Q11 22 20 12" fill="none" stroke="#fff" stroke-width="1.5"/></svg>
    <div><b>Improved Patient Satisfaction</b>Patient care is focused on prevention to keep patients out of the hospital by supporting patients between visits.</div>
  </div>
  <div class="perk" style="top:520px">
    <svg class="ico" viewBox="0 0 22 22"><circle cx="11" cy="6" r="4" fill="#fff"/><path d="M3 21 C3 13 19 13 19 21Z" fill="#fff"/><path d="M11 14v6M8 17h6" stroke="var(--blue)" stroke-width="2"/></svg>
    <div><b>Improved Care Coordination</b>Referral coordination helps keep patients out of the hospital and prevents patients from "falling through the cracks."</div>
  </div>
  <div class="perk" style="top:568px">
    <svg class="ico" viewBox="0 0 22 22"><circle cx="11" cy="11" r="10" fill="#fff"/><circle cx="11" cy="11" r="8" fill="none" stroke="var(--blue)" stroke-width="1.2"/><text x="11" y="15" text-anchor="middle" font-family="Arimo,Arial,sans-serif" font-weight="700" font-size="11" fill="var(--blue)">$</text></svg>
    <div><b>Increased Revenue</b>CCM Increases Income for the clinic by billing CCM services.</div>
  </div>
</section>

</body>
</html>
```